Marwick Law Letterhead

We need a new letterhead design for a Law Firm. The address for the law firm is 1475 Calloway Street, Suite 210, Houston, Texas 77041. Phone Number: 832-361-9027; Fax Number: 832-614-7359. The logo is uploaded to the project.

```html
<!DOCTYPE html>
<html lang="en">
<head>
<meta charset="utf-8">
<title>Marwick Law Letterhead</title>
<link href="https://fonts.googleapis.com/css2?family=Montserrat:wght@400;500&display=swap" rel="stylesheet">
<style>
  :root {
    --backdrop: #e8e8e8;
    --paper: #ffffff;
    --navy: #1c2c5b;
    --red: #e01b24;
    --deep-red: #6a0009;
    --ink: #2b2b2b;
    --ink-dark: #111111;
  }
  html, body {
    margin: 0;
    width: 1154px;
    height: 1200px;
    overflow: hidden;
    background: var(--backdrop);
    font-family: "Montserrat", sans-serif;
  }
  .letterhead {
    position: absolute;
    left: 169px;
    top: 30px;
    width: 816px;
    height: 1140px;
    background: var(--paper);
    box-shadow: 0 6px 24px rgba(0,0,0,0.12);
  }
  .brand {
    position: absolute;
    left: 30px;
    top: 92px;
    display: flex;
    align-items: center;
    gap: 14px;
  }
  .brand-mark {
    width: 22px;
    height: 22px;
    background: var(--navy);
  }
  .brand-name {
    font-weight: 500;
    font-size: 34px;
    color: var(--navy);
    letter-spacing: 0.5px;
  }
  .header-rule {
    position: absolute;
    left: 29px;
    top: 197px;
    width: 756px;
    height: 5px;
    background: var(--red);
  }
  .letter-date {
    position: absolute;
    right: 32px;
    top: 262px;
    font-size: 14.5px;
    color: var(--ink-dark);
  }
  .recipient {
    position: absolute;
    left: 31px;
    top: 275px;
    font-size: 14px;
    line-height: 20.3px;
    color: var(--ink-dark);
  }
  .letter-flow {
    position: absolute;
    left: 32px;
    top: 359px;
    width: 755px;
  }
  .letter-body {
    font-size: 13.2px;
    line-height: 20.3px;
    color: var(--ink);
  }
  .letter-body p {
    margin: 0 0 20.3px;
    text-align: justify;
    hyphens: auto;
    -webkit-hyphens: auto;
  }
  .letter-body p:last-child { margin-bottom: 0; }
  .closing {
    margin: 24px 0 0 -2px;
    font-size: 17px;
    color: var(--ink-dark);
  }
  .signature {
    margin: 12px 0 0 -4px;
    width: 92px;
    height: 28px;
    background: linear-gradient(90deg, #d8d8d8, #c4c4c4);
    border-radius: 3px;
  }
  .footer-band {
    position: absolute;
    top: 1072px;
    height: 13px;
    background: linear-gradient(90deg, var(--red), var(--deep-red));
  }
  .footer-band.left { left: 0; width: 257px; }
  .footer-band.right { left: 525px; width: 291px; }
  .footer-contacts {
    position: absolute;
    left: 270px;
    top: 1068px;
    display: flex;
    align-items: center;
    gap: 6px;
    font-size: 14px;
    color: var(--ink-dark);
  }
  .footer-contacts svg { width: 13px; height: 13px; margin-left: 8px; }
  .footer-address {
    position: absolute;
    left: 0;
    width: 816px;
    top: 1096px;
    text-align: center;
    font-size: 14px;
    color: var(--ink-dark);
  }
</style>
</head>
<body>
<main class="letterhead">
  <div class="brand">
    <span class="brand-mark"></span>
    <span class="brand-name">Marwick Law</span>
  </div>
  <div class="header-rule"></div>

  <div class="letter-date">DATE:05-Jan-2022</div>
  <div class="recipient">
    Mr/s<br>First Name and Last Name<br>Company Name<br>Address
  </div>

  <section class="letter-flow">
    <div class="letter-body">
      <p>Lorem ipsum dolor sit amet,consectetur adipiscing sed do eiusmod tempor incididunt laboreet dolore magna aliqua.Ut enim ad minim.veniam, quis nostrud exercitation ullamco laboris nisi ut aliquip exea commodo consequat.Lorem ipsum dolor sit amet,consectetur adipiscing sed do eiusmod tempor incididunt.labore et dolore magna aliqua. Ut enim</p>
      <p>Lorem ipsum dolor sit amet, consectetur adipiscing sed do eiusmod tempor incididunt labore et dolore magna aliqua. Ut enim ad minim veniam, quis nostrud exercitation ullamco laboris nisi ut aliquip exea commodo consequat.Duis aute irure dolor in reprehenderit in voluptate velit esse cillum irure dolor in reprehenderit in voluptate velit esse irure</p>
      <p>Lorem ipsum dolor sit amet, consectetur adipiscing sed do eiusmod tempor incididunt labore et dolore magna aliqua. consequat. Duis aute irure dolor in.reprehenderit in voluptate velit esse cillum dolore eu fugiat nulla pariatur. Excepteur sint occaecat cupidatat non proident, sunt in culpa qui officia deserunt mollit,</p>
      <p>Lorem ipsum dolor sit amet, consectetur adipiscing sed do eiusmod tempor incididunt labore et dolore magna aliqua. Ut enim Lorem ipsum dolor sit amet, consectetur adipiscing sed do eiusmod tempor incididunt labore et dolore magna aliqua. Ut enim Lorem ipsum aliqua.ipsum</p>
      <p>Lorem ipsum dolor sit amet, consectetur adipiscing sed do eiusmod tempor incididunt labore et dolore magna aliqua. Ut enim ad minim veniam, quis nostrud exercitation ullamco laboris nisi ut aliquip exea commodo consequat.Duis aute irure dolor in reprehenderit in voluptate velit esse cillum irure dolor in reprehenderit in voluptate velit esse irure</p>
      <p>Lorem ipsum dolor sit amet, consectetur adipiscing sed do eiusmod tempor incididunt labore et dolore magna aliqua. Ut enim ad minim veniam, quis nostrud exercitation ullamco laboris nisi ut aliquip exea commodo consequat.Duis aute irure dolor in reprehenderit in voluptate velit esse cillum irure dolor in reprehenderit in voluptate velit esse irure</p>
    </div>
    <div class="closing">Regards</div>
    <div class="signature" role="img" aria-label="Handwritten signature of the sender"></div>
  </section>

  <div class="footer-band left"></div>
  <div class="footer-contacts">
    <svg viewBox="0 0 16 16" aria-hidden="true"><path fill="#e01b24" d="M3.6 1.5l2.2 2.6-1.3 1.6c.9 2 2.4 3.5 4.4 4.4l1.6-1.3 2.6 2.2-1.4 2.2C6.8 13.2 2.8 9.2 1.4 4.3z"/></svg>
    <span>832-361-9027</span>
    <svg viewBox="0 0 16 16" aria-hidden="true"><rect x="4" y="1.5" width="8" height="4" fill="#e01b24"/><rect x="1.5" y="5.5" width="13" height="6" rx="1" fill="#e01b24"/><rect x="4" y="9.5" width="8" height="5" fill="#fff" stroke="#e01b24" stroke-width="1.2"/></svg>
    <span>832-614-7359</span>
  </div>
  <div class="footer-band right"></div>
  <div class="footer-address">1475 Calloway Street, Suite 210, Houston, Texas 77041</div>
</main>
</body>
</html>
```